KDWB Business Card

Looking for a business card design to incorporate our branding. We want to only use the colors listing in the Branding Package (attached).
Updates

Target Market(s)

People who need their phone or device fixed.

Industry/Entity Type

Electronics

Contact Information for Business Card

Please use:

Brightwick Gadget Clinic LLC
4810 E Harlow Ridge Rd
Suite 417
San Antonio, TX 78163

Marcus Delgrove, Store Manager

(210) 555-0147

Requirements
Must have
• Must include the colors that are contained within the Branding Package PDF file.

```html
<!DOCTYPE html>
<html lang="en">
<head>
<meta charset="utf-8">
<title>Brightwick Gadget Clinic – Business Card</title>
<link rel="stylesheet" href="https://fonts.googleapis.com/css2?family=Arimo:wght@400&display=swap">
<style>
  :root {
    --brand-orange: #f15a24;
    --charcoal: #58595b;
    --ink: #3a3a3a;
    --paper: #ffffff;
    --backdrop: #e4e4e4;
  }
  html, body {
    margin: 0;
    padding: 0;
    width: 1189px;
    height: 1200px;
    overflow: hidden;
    background: var(--backdrop);
    font-family: "Arimo", Arial, sans-serif;
  }
  .canvas { position: relative; width: 1189px; height: 1200px; }
  .card {
    position: absolute;
    left: 263px;
    width: 663px;
    height: 392px;
    background: var(--paper);
    overflow: hidden;
  }
  .card--front { top: 188px; }
  .card--back { top: 620px; }

  .brand {
    position: absolute;
    display: flex;
    align-items: center;
    gap: 12px;
    transform: translate(-50%, -50%);
    white-space: nowrap;
  }
  .brand__square {
    width: 40px;
    height: 40px;
    background: var(--brand-orange);
    border-radius: 6px;
    flex: none;
  }
  .brand__name {
    color: var(--brand-orange);
    font-size: 26px;
    font-weight: 400;
    letter-spacing: 0.2px;
  }
  .card--front .brand { left: 332px; top: 196px; }
  .card--back .brand { left: 177px; top: 175px; }
  .card--back .brand__name { font-size: 22px; }
  .card--back .brand__square { width: 34px; height: 34px; }

  .divider {
    position: absolute;
    left: 354px;
    top: 73px;
    width: 2px;
    height: 222px;
    background: var(--charcoal);
  }
  .contact { position: absolute; left: 380px; top: 143px; color: var(--ink); }
  .contact__phone {
    display: flex;
    align-items: center;
    gap: 10px;
    font-size: 16px;
  }
  .contact__name { margin-top: 12px; font-size: 21px; }
  .contact__role { margin-top: 4px; font-size: 13px; color: var(--brand-orange); }

  .footer-band { position: absolute; left: 0; top: 326px; width: 663px; height: 66px; }
  .address {
    position: absolute;
    left: 353px;
    top: 344px;
    color: var(--paper);
    font-size: 13px;
    line-height: 16px;
    letter-spacing: 0.4px;
  }
  .address__pin { position: absolute; left: -28px; top: 2px; }
</style>
</head>
<body>
<main class="canvas">
  <section class="card card--front" aria-label="Card front">
    <div class="brand">
      <span class="brand__square"></span>
      <span class="brand__name">Brightwick Gadget Clinic</span>
    </div>
  </section>

  <section class="card card--back" aria-label="Card back">
    <div class="brand">
      <span class="brand__square"></span>
      <span class="brand__name">Brightwick Gadget Clinic</span>
    </div>

    <div class="divider"></div>

    <div class="contact">
      <div class="contact__phone">
        <svg width="15" height="15" viewBox="0 0 15 15" aria-hidden="true">
          <rect width="15" height="15" fill="var(--brand-orange)"/>
          <path d="M4.5 3.5c.6-.5 1.2-.4 1.5.1l.8 1.3c.2.4.1.8-.2 1.1l-.5.4c.4 1 1.2 1.8 2.2 2.3l.4-.5c.3-.3.7-.4 1.1-.2l1.3.8c.5.3.6.9.1 1.5-.7.8-1.7 1-2.7.5C6.6 9.9 5.1 8.4 4.2 6.5c-.5-1-.4-2.2.3-3z" fill="#fff"/>
        </svg>
        <span>(210) 555-0147</span>
      </div>
      <div class="contact__name">Marcus Delgrove</div>
      <div class="contact__role">Store Manager</div>
    </div>

    <svg class="footer-band" viewBox="0 0 663 66" aria-hidden="true">
      <rect x="0" y="0" width="663" height="66" fill="var(--charcoal)"/>
      <polygon points="296,7 663,7 663,66 255,66" fill="var(--paper)"/>
      <polygon points="304,10 663,10 663,66 264,66" fill="var(--brand-orange)"/>
    </svg>

    <div class="address">
      <svg class="address__pin" width="13" height="13" viewBox="0 0 13 13" aria-hidden="true">
        <rect width="13" height="13" fill="var(--paper)"/>
        <path d="M6.5 2.2a2.8 2.8 0 0 1 2.8 2.8c0 2-2.8 5-2.8 5S3.7 7 3.7 5a2.8 2.8 0 0 1 2.8-2.8z" fill="var(--brand-orange)"/>
        <circle cx="6.5" cy="5" r="1" fill="var(--paper)"/>
      </svg>
      <div>4810 E Harlow Ridge Rd</div>
      <div>Suite 417, San Antonio, TX 78163</div>
    </div>
  </section>
</main>
</body>
</html>
```